VENTURE CAPITAL GROUP BUSINESS CARD DESIGN

Venture Capital Group based in SF looking for a bold business card design. No trendy colour explosion, 3D effects etc. Just "simple" optical effects. Works on your brain, keeps your eye focused and sticks to your mind.
Target Market(s)
Technology startups
Industry/Entity Type
Venture Capital
Contact Information for Business Card
DESMOND WHITLAKE
MANAGING PARTNER
187 FENWORTH ST SAN FRANCISCO, CA 94187
415.555.0142 O
415.555.0147 F
415.555.0193 C
desmond@veldtmoorcapital.ventures

```html
<!DOCTYPE html>
<html lang="en">
<head>
<meta charset="utf-8">
<title>Veldtmoor Capital Group – Business Card</title>
<link href="https://fonts.googleapis.com/css2?family=Cinzel:wght@400;600&family=Open+Sans:wght@400;700&display=swap" rel="stylesheet">
<style>
  :root {
    --bg: #e9e6e1;
    --green-light: #55b652;
    --green-mid: #2f8f3a;
    --green-dark: #0b5a24;
    --white: #ffffff;
    --paper-shade: #eeeeee;
    --circle-grey: #dcdcdc;
    --brand-green: #1f8a35;
  }
  * { box-sizing: border-box; margin: 0; padding: 0; }
  html, body { width: 1200px; height: 900px; overflow: hidden; }
  body {
    background: var(--bg);
    position: relative;
    font-family: "Open Sans", Arial, sans-serif;
  }
  .card {
    position: absolute;
    width: 520px;
    height: 298px;
    border-radius: 3px;
    overflow: hidden;
    box-shadow: 0 6px 18px rgba(0,0,0,0.18);
  }
  .card--front {
    left: 70px; top: 150px;
    background: linear-gradient(180deg, var(--green-light) 0%, var(--green-mid) 50%, var(--green-dark) 100%);
  }
  .card--back {
    left: 610px; top: 450px;
    background: var(--white);
  }
  .brand {
    position: absolute;
    display: flex;
    align-items: center;
    gap: 16px;
  }
  .brand__circle {
    width: 66px; height: 66px;
    border-radius: 50%;
    flex: none;
  }
  .brand__name {
    font-family: "Cinzel", Georgia, serif;
    font-weight: 400;
    font-size: 28px;
    letter-spacing: 1px;
    line-height: 1;
  }
  .brand__tag {
    font-family: "Cinzel", Georgia, serif;
    font-weight: 400;
    font-size: 8px;
    letter-spacing: 4px;
    text-align: center;
    margin-top: 3px;
  }
  .card--front .brand { left: 96px; top: 112px; color: var(--white); }
  .card--front .brand__circle { background: var(--white); }

  .back__top {
    position: absolute; inset: 0 0 auto 0; height: 150px;
    background: linear-gradient(180deg, var(--white) 0%, var(--paper-shade) 100%);
  }
  .card--back .brand { left: 96px; top: 40px; color: var(--brand-green); }
  .card--back .brand__circle { background: radial-gradient(circle at 40% 35%, var(--white), var(--circle-grey)); }

  .back__band {
    position: absolute; left: 0; right: 0; top: 150px; bottom: 0;
    background: linear-gradient(180deg, var(--green-light) 0%, var(--green-mid) 55%, var(--green-dark) 100%);
    color: var(--white);
  }
  .person { position: absolute; left: 290px; top: -4px; }
  .person__name { font-weight: 700; font-size: 17px; }
  .person__title { font-size: 11.5px; margin-top: 1px; }
  .phones {
    position: absolute; right: 250px; top: 24px;
    list-style: none; text-align: right;
    font-size: 13px; line-height: 21px;
  }
  .phones li { display: flex; justify-content: flex-end; align-items: center; gap: 6px; }
  .phones svg { width: 11px; height: 11px; fill: var(--white); flex: none; }
  .address {
    position: absolute; left: 290px; top: 40px;
    font-size: 12px; line-height: 18px; font-style: normal;
  }
  .email {
    position: absolute; left: 34px; bottom: 24px;
    font-size: 15.5px;
  }
</style>
</head>
<body>
  <section class="card card--front" aria-label="Business card front">
    <div class="brand">
      <span class="brand__circle"></span>
      <div>
        <div class="brand__name">VELDTMOOR</div>
        <div class="brand__tag">CAPITAL GROUP</div>
      </div>
    </div>
  </section>

  <section class="card card--back" aria-label="Business card back">
    <div class="back__top">
      <div class="brand">
        <span class="brand__circle"></span>
        <div>
          <div class="brand__name">VELDTMOOR</div>
          <div class="brand__tag">CAPITAL GROUP</div>
        </div>
      </div>
    </div>
    <div class="back__band">
      <div class="person">
        <div class="person__name">Desmond Whitlake</div>
        <div class="person__title">Managing Partner</div>
      </div>
      <ul class="phones">
        <li>415.555.0142
          <svg viewBox="0 0 24 24" aria-label="Office"><path d="M6.6 10.8a15.1 15.1 0 0 0 6.6 6.6l2.2-2.2c.3-.3.7-.4 1-.2 1.1.4 2.3.6 3.6.6.6 0 1 .4 1 1V20c0 .6-.4 1-1 1A17 17 0 0 1 3 4c0-.6.4-1 1-1h3.5c.6 0 1 .4 1 1 0 1.3.2 2.5.6 3.6.1.3 0 .7-.2 1z"/></svg></li>
        <li>415.555.0147
          <svg viewBox="0 0 24 24" aria-label="Fax"><path d="M6 2h9l3 3v5H6zM3 11h18v9H3zm3 3v2h6v-2z"/></svg></li>
        <li>415.555.0193
          <svg viewBox="0 0 24 24" aria-label="Mobile"><path d="M7 1h10a2 2 0 0 1 2 2v18a2 2 0 0 1-2 2H7a2 2 0 0 1-2-2V3a2 2 0 0 1 2-2zm0 3v15h10V4z"/></svg></li>
        <li>desmond@veldtmoorcapital.ventures
          <svg viewBox="0 0 24 24" aria-label="Email"><path d="M2 5h20v14H2zm2 2v.5l8 5 8-5V7l-8 5z"/></svg></li>
      </ul>
      <address class="address">187 Fenworth St San<br>Francisco, CA 94187</address>
    </div>
  </section>
</body>
</html>
```